Timber Crest Construction Needs business card

Hey we are in need of business card designs. I have upload our logo as a guideline, but free feel to run with it or come up with something unique.
Pls have fun with it and be creative. the name says it all!
i will give some directions after i see a few entries..
Updates
Logo source file has been uploaded..
Hey because of the logo is so colourful already.
Can we have a few submissions with less colour.
Also we are looking for clever/hidden/descriptive business card.

```html
<!DOCTYPE html>
<html lang="en">
<head>
<meta charset="utf-8">
<title>Timber Crest Construction – Business Card</title>
<link rel="stylesheet" href="https://fonts.googleapis.com/css2?family=Didact+Gothic&family=Montserrat:wght@600;700&display=swap">
<style>
  :root {
    --stage: #1f7c0c;
    --card-dark: #000000;
    --card-light: #ffffff;
    --brand-grey: #808083;
    --ink: #1a1a1a;
    --accent-red: #e5202a;
    --base-band: #333335;
  }
  * { box-sizing: border-box; margin: 0; padding: 0; }
  html, body { width: 1200px; height: 1200px; overflow: hidden; }
  body {
    position: relative;
    background: var(--stage);
    font-family: "Didact Gothic", "Century Gothic", sans-serif;
  }
  .card {
    position: absolute;
    left: 212px;
    width: 800px;
    height: 445px;
  }
  .card--back { top: 130px; background: var(--card-dark); }
  .card--front { top: 641px; height: 444px; background: var(--card-light); overflow: hidden; }

  .wordmark {
    position: absolute;
    font-family: "Montserrat", sans-serif;
    font-weight: 700;
    color: var(--brand-grey);
    white-space: nowrap;
    text-transform: uppercase;
    letter-spacing: -0.5px;
  }
  .card--back .wordmark {
    left: 0; right: 0;
    top: 240px;
    text-align: center;
    font-size: 34px;
  }
  .card--front .wordmark {
    left: 88px;
    top: 102px;
    font-size: 30px;
  }

  .person {
    position: absolute;
    right: 100px;
    top: 196px;
    text-align: right;
  }
  .person__name {
    font-family: "Montserrat", sans-serif;
    font-weight: 700;
    font-size: 15px;
    letter-spacing: 3px;
    color: var(--ink);
  }
  .person__role {
    margin-top: 4px;
    font-size: 14px;
    letter-spacing: 3px;
    color: var(--accent-red);
  }

  .contacts {
    position: absolute;
    left: 88px;
    top: 277px;
    list-style: none;
  }
  .contacts li {
    display: flex;
    align-items: center;
    height: 25px;
    font-size: 15px;
    letter-spacing: 2.6px;
    color: var(--ink);
  }
  .contacts svg {
    width: 16px;
    height: 16px;
    margin-right: 21px;
    fill: none;
    stroke: var(--accent-red);
    stroke-width: 1.6;
  }

  .address {
    position: absolute;
    right: 99px;
    top: 330px;
    text-align: right;
    font-size: 14.5px;
    line-height: 21px;
    letter-spacing: 2.6px;
    color: var(--ink);
    font-style: normal;
    text-transform: uppercase;
  }

  .base-band {
    position: absolute;
    left: 0;
    bottom: 0;
    width: 800px;
    height: 14px;
    background: var(--base-band);
  }
</style>
</head>
<body>

  <section class="card card--back" aria-label="Card back">
    <div class="wordmark">Timber Crest Construction</div>
  </section>

  <section class="card card--front" aria-label="Card front">
    <div class="wordmark">Timber Crest Construction</div>

    <div class="person">
      <div class="person__name">MARTEN HALE</div>
      <div class="person__role">DIRECTOR</div>
    </div>

    <ul class="contacts">
      <li>
        <svg viewBox="0 0 16 16" aria-hidden="true"><path d="M2 6c0-2 2.5-3 6-3s6 1 6 3v1h-3V5.5H5V7H2z"/><path d="M4 9h8l1 5H3z"/><circle cx="8" cy="11" r="1.2"/></svg>
        9518 2247
      </li>
      <li>
        <svg viewBox="0 0 16 16" aria-hidden="true"><rect x="4" y="2" width="8" height="4"/><rect x="2" y="6" width="12" height="6"/><rect x="4" y="10" width="8" height="4"/></svg>
        9518 2290
      </li>
      <li>
        <svg viewBox="0 0 16 16" aria-hidden="true"><rect x="1.5" y="3.5" width="13" height="9"/><path d="M1.5 3.5 8 9l6.5-5.5M1.5 12.5 6 7.5M14.5 12.5 10 7.5"/></svg>
        marten@harlowreeve.com
      </li>
      <li>
        <svg viewBox="0 0 16 16" aria-hidden="true"><circle cx="8" cy="8" r="6"/><ellipse cx="8" cy="8" rx="2.6" ry="6"/><path d="M2 8h12M3 5h10M3 11h10"/></svg>
        www.harlowreeve.com
      </li>
    </ul>

    <address class="address">
      Shop 3, 212-216 Calder<br>
      Road Westmere North
    </address>

    <div class="base-band" aria-hidden="true"></div>
  </section>

</body>
</html>
```